Business Cards for new orthopaedic surgery practice

My husband and I are starting our own orthopaedic surgery practice. We are looking for a business card that is uniform, but one will have my name/title and the other will have his. You can just create one design with my name on it for now. But when I choose your design as the winning design I will ask that you add another copy with his name/title.

We are looking for classy, simple, elite all in one. We like dark blues/a little gold/yellow. Something that goes with our logo. We want our logo incorporated. Here is all the info you need:
Business name: RV Bone & Vitality Center
Location: 38517 North Willowmere Ave
Maple Hollow, FL 33990
Phone: 954-218-4063
Fax: 954-582-7341
Email: info@myrvbonecare.example

Names: Lydia Vance, M.D.
Board Certified Hand and Upper Extremity Surgeon

Ebo Dansu, M.D.
Board Certified Hip & Knee Replacement/General Orthopaedic Surgeon

Can decide what you want to put on the back. Maybe a slogan:
Grounded in Care. Centered on You

I am just going to upload our logo. The only thing is if we select you as the winning design, the location, and phone numbers may change. We will need your help to update that once fully solidified.

Industry/Entity Type

Medical

Contact Information for Business Card

Colors
0054AA
0677BA
7BADD7
CADEEF
E8F1F8
0094D4
00A9DD
6FCCEA
C7EBF8
E9F6FB

Requirements
Must have
• class, appeal,
Should not have
• We want to air on the side of masculine if we are looking at masculine vs. feminine feel. But we still want it classy, sophisticated, and something we will love

```html
<!DOCTYPE html>
<html lang="en">
<head>
<meta charset="utf-8">
<title>RV Bone &amp; Vitality Center — Business Cards</title>
<link rel="stylesheet" href="https://fonts.googleapis.com/css2?family=Cinzel:wght@600;700&family=Montserrat:wght@400;500&display=swap">
<style>
  :root {
    --backdrop: #1c1c1e;
    --navy: #1b2850;
    --navy-deep: #15203f;
    --navy-light: #2a3d6b;
    --gold: #c9a45c;
    --white: #ffffff;
  }
  * { box-sizing: border-box; margin: 0; padding: 0; }
  html, body { width: 1200px; height: 1200px; overflow: hidden; }
  body {
    background: var(--backdrop);
    display: flex; align-items: center; justify-content: center; gap: 60px;
    font-family: "Montserrat", sans-serif; color: var(--white);
  }
  .card {
    width: 440px; height: 760px; border-radius: 30px;
    background: var(--navy);
    position: relative; overflow: hidden;
    display: flex; flex-direction: column; align-items: center;
  }
  .brand {
    display: flex; flex-direction: column; align-items: center; gap: 16px;
    text-align: center;
  }
  .brand-dot { width: 26px; height: 26px; border-radius: 50%; border: 2px solid var(--gold); }
  .brand-name {
    font-family: "Cinzel", serif; font-weight: 600; color: var(--white);
    font-size: 27px; line-height: 1.3; letter-spacing: 2px;
  }
  .card-front .brand { margin-top: 110px; }
  .doctor { margin-top: 80px; text-align: center; }
  .doctor-name {
    font-family: "Cinzel", serif; font-weight: 700; color: var(--gold);
    font-size: 28px; letter-spacing: 0.5px;
  }
  .doctor-title { font-size: 17px; line-height: 1.3; margin-top: 6px; }
  .contact-divider {
    display: flex; align-items: center; gap: 10px; margin-top: 30px;
  }
  .contact-divider .rule { width: 70px; height: 1px; background: var(--gold); }
  .icon { width: 26px; height: 26px; }
  .contact-lines { margin-top: 22px; text-align: center; font-size: 18px; line-height: 1.5; }
  .gold-rule { width: 200px; height: 1px; background: var(--gold); margin: 14px 0; }
  .address { text-align: center; font-size: 18px; line-height: 1.45; }
  .card-back {
    background: linear-gradient(160deg, var(--navy-light) 0%, var(--navy) 45%, var(--navy-deep) 100%);
    justify-content: center;
  }
  .slogan {
    position: absolute; bottom: 70px; left: 0; right: 0; text-align: center;
    color: var(--gold); font-size: 20px; font-weight: 500;
  }
</style>
</head>
<body>
  <section class="card card-front">
    <div class="brand">
      <span class="brand-dot"></span>
      <div class="brand-name">RV Bone &amp;<br>Vitality Center</div>
    </div>
    <div class="doctor">
      <div class="doctor-name">LYDIA VANCE, M.D.</div>
      <div class="doctor-title">Board Certified Hand and Upper<br>Extremity Surgeon</div>
    </div>
    <div class="contact-divider">
      <span class="rule"></span>
      <svg class="icon" viewBox="0 0 26 26" aria-label="Phone"><circle cx="13" cy="13" r="12" fill="none" stroke="#c9a45c" stroke-width="1.5"/><path d="M9 7.5l2 .2 1 3-1.3 1.1a7 7 0 003.5 3.5l1.1-1.3 3 1 .2 2c-5 1.2-10.7-4.5-9.5-9.5z" fill="none" stroke="#c9a45c" stroke-width="1.2"/></svg>
      <svg class="icon" viewBox="0 0 26 26" aria-label="Fax"><circle cx="13" cy="13" r="12" fill="none" stroke="#c9a45c" stroke-width="1.5"/><rect x="9.5" y="7" width="7" height="4" fill="#c9a45c"/><rect x="7" y="11" width="12" height="6" rx="1" fill="#c9a45c"/><rect x="9.5" y="15" width="7" height="4" fill="#c9a45c" stroke="#1b2850"/></svg>
      <svg class="icon" viewBox="0 0 26 26" aria-label="Email"><circle cx="13" cy="13" r="12" fill="none" stroke="#c9a45c" stroke-width="1.5"/><rect x="7" y="9" width="12" height="8" fill="#c9a45c"/><path d="M7 9l6 5 6-5" fill="none" stroke="#1b2850" stroke-width="1"/></svg>
      <span class="rule"></span>
    </div>
    <div class="contact-lines">
      <div>954-218-4063</div>
      <div>954-582-7341</div>
      <div>info@myrvbonecare.example</div>
    </div>
    <div class="gold-rule"></div>
    <div class="address">38517 North Willowmere Ave<br>Maple Hollow, FL 33990</div>
  </section>

  <section class="card card-back">
    <div class="brand">
      <span class="brand-dot"></span>
      <div class="brand-name">RV Bone &amp;<br>Vitality Center</div>
    </div>
    <div class="slogan">Grounded in Care. Centered on You</div>
  </section>
</body>
</html>
```